Business Card Design

We are a manufacturing and distribution company with most of our customer base being supermarkets. We have established brand guidelines that are attached.

```html
<!DOCTYPE html>
<html lang="en">
<head>
<meta charset="utf-8">
<title>Varnelle Business Card</title>
<link rel="stylesheet" href="https://fonts.googleapis.com/css2?family=Poppins:wght@400;500;600;700&display=swap">
<style>
  :root {
    --bg: #2a2a2c;
    --card: #1c1d1f;
    --card-back-light: #3a3b3d;
    --card-back-dark: #0e0e0f;
    --white: #e9eaea;
    --text: #f1f1f1;
    --red: #e51d27;
    --blue: #0a6cb6;
    --rule: #77787a;
  }
  * { box-sizing: border-box; margin: 0; padding: 0; }
  html, body { width: 1200px; height: 1108px; overflow: hidden; }
  body {
    background: var(--bg);
    font-family: "Poppins", sans-serif;
    position: relative;
  }
  .card {
    position: absolute;
    top: 184px;
    width: 460px;
    height: 740px;
    border-radius: 26px;
    overflow: hidden;
  }
  .card-front {
    left: 110px;
    background: var(--card);
    color: var(--text);
    text-align: center;
  }
  .card-back { left: 630px; }

  .brand {
    position: absolute;
    top: 190px;
    left: 0; right: 0;
    display: flex;
    justify-content: center;
    align-items: center;
    gap: 16px;
  }
  .brand-square {
    width: 30px; height: 30px;
    background: var(--red);
  }
  .brand-name {
    font-weight: 600;
    font-size: 52px;
    letter-spacing: 2px;
    color: var(--white);
    line-height: 1;
  }

  .person {
    position: absolute;
    top: 398px;
    left: 0; right: 0;
  }
  .person-name {
    font-weight: 700;
    font-size: 27px;
    letter-spacing: 1px;
    line-height: 1.1;
  }
  .person-name .first { color: var(--red); }
  .person-name .last { color: var(--blue); }
  .person-title {
    font-size: 18px;
    font-weight: 400;
    margin-top: 2px;
  }

  .icon-row {
    position: absolute;
    top: 482px;
    left: 50px; right: 50px;
    display: flex;
    align-items: center;
    gap: 8px;
  }
  .icon-row .rule { flex: 1; height: 1px; background: var(--rule); }
  .icon {
    width: 30px; height: 30px;
    border-radius: 5px;
    background: var(--red);
    display: flex; align-items: center; justify-content: center;
  }
  .icon svg { width: 18px; height: 18px; }

  .contact {
    position: absolute;
    top: 526px;
    left: 0; right: 0;
    font-size: 19px;
    line-height: 1.4;
  }
  .divider {
    position: absolute;
    top: 636px;
    left: 60px; right: 60px;
    height: 1px;
    background: #4a4b4d;
  }
  .address {
    position: absolute;
    top: 652px;
    left: 0; right: 0;
    font-size: 18px;
    line-height: 1.35;
  }

  .back-pattern {
    position: absolute; inset: 0;
    background: linear-gradient(160deg, var(--card-back-light) 0%, #202123 55%, var(--card-back-dark) 100%);
  }
  .back-brand {
    position: absolute;
    left: 0; right: 0;
    top: 520px;
    display: flex;
    justify-content: center;
    align-items: center;
    gap: 10px;
  }
  .back-brand .brand-square { width: 16px; height: 16px; }
  .back-brand .brand-name { font-size: 22px; letter-spacing: 1px; }
</style>
</head>
<body>

<section class="card card-front">
  <div class="brand">
    <span class="brand-square"></span>
    <span class="brand-name">VARNELLE</span>
  </div>

  <div class="person">
    <p class="person-name"><span class="first">MARCUS</span> <span class="last">HALE</span></p>
    <p class="person-title">Managing Director</p>
  </div>

  <div class="icon-row">
    <span class="rule"></span>
    <span class="icon" aria-label="Phone">
      <svg viewBox="0 0 24 24"><path fill="#1c1d1f" d="M6.6 10.8a15 15 0 0 0 6.6 6.6l2.2-2.2c.3-.3.7-.4 1-.2 1.1.4 2.3.6 3.6.6.6 0 1 .4 1 1V20c0 .6-.4 1-1 1A17 17 0 0 1 3 4c0-.6.4-1 1-1h3.5c.6 0 1 .4 1 1 0 1.2.2 2.4.6 3.6.1.3 0 .7-.2 1z"/></svg>
    </span>
    <span class="icon" aria-label="Email">
      <svg viewBox="0 0 24 24"><rect x="3" y="6" width="18" height="12" rx="1" fill="none" stroke="#1c1d1f" stroke-width="2"/><path d="M3 7l9 6 9-6" fill="none" stroke="#1c1d1f" stroke-width="2"/></svg>
    </span>
    <span class="icon" aria-label="Website">
      <svg viewBox="0 0 24 24"><circle cx="12" cy="12" r="9" fill="none" stroke="#1c1d1f" stroke-width="2"/><path d="M3 12h18M12 3c3 3 3 15 0 18M12 3c-3 3-3 15 0 18" fill="none" stroke="#1c1d1f" stroke-width="1.6"/></svg>
    </span>
    <span class="rule"></span>
  </div>

  <div class="contact">
    <p>044-987 654 321</p>
    <p>hello@varnelle.com</p>
    <p>www.varnelle-foods.com</p>
  </div>

  <div class="divider"></div>

  <div class="address">
    <p>88, Foundry Lane West</p>
    <p>30917, Northland</p>
  </div>
</section>

<section class="card card-back">
  <div class="back-pattern" role="img" aria-label="Repeating embossed brand-mark pattern on black"></div>
  <div class="back-brand">
    <span class="brand-square"></span>
    <span class="brand-name">VARNELLE</span>
  </div>
</section>

</body>
</html>
```